Fitness Centre/Personal Trainer Business Card

We need a business card design for a company based in Singapore called 'Vigor Ledger'.

We are a team of Personal Trainers and we are planning to open our new training facility.

This design will also be printed/painted on the walls in our gym.

We are a new breed of personal trainers who take fitness seriously and holistically. We do not merely train our clients to be big and muscular.

We believe in wholeness. In our opinion, fitness should include: strength, speed, flexibility, mobility, stamina & agility. These are what we train for. Of course, nutrition/diet is key.

We use fitness tools such as kettlebells, QVL, Pylometric boxes, battling ropes, clubbells, medicine balls, bulgarian bags etc - functional and non-bulky tools.

I currently have a Facebook page 'Vigor Ledger SG' which shows a logo of a kettlebell. But my business focus has since changed.

Services provided:
- Kettlebell Sport Preparation
- Calisthenics Training
- Corrective Exercises
- Sports Strength & Conditioning
- 28 days Weight Loss Program
- Myofascial Rehab Therapy
- Sports/Thai Massage

Main colors for the design should be BLACK & YELLOW. We envision a design which is able to protray the holistic view we take on fitness. Also it should somewhat appeal to the ladies and not intimidate them.

Target Market(s)

People between 18-35 years old. Students and working class alike.

Industry/Entity Type

Training

Requirements
Must have
• Name: Marcus Obadiah Lim
Fitness Coach
Corrective Exercise Specialist
M: +65 9437 2065
E: marcus@sgvigorledger-example.com

Double-sided please.
Nice to have
• "What is your vigor ledger?"

```html
<!DOCTYPE html>
<html lang="en">
<head>
<meta charset="utf-8">
<title>Vigor Ledger – Business Cards</title>
<link rel="stylesheet" href="https://fonts.googleapis.com/css2?family=Open+Sans:wght@400;600;700;800&display=swap">
<style>
  :root {
    --ink: #0b0b0b;
    --paper: #ffffff;
    --yellow: #f6d000;
    --yellow-text: #f2cf1d;
    --grey-band: #9c9c9c;
    --text-dark: #222222;
    --text-muted: #555555;
    --stage-light: #e4e4e4;
    --stage-dark: #a9a9a9;
  }
  * { box-sizing: border-box; margin: 0; padding: 0; }
  html, body { width: 1200px; height: 499px; overflow: hidden; }
  body {
    font-family: "Open Sans", Arial, sans-serif;
    background: radial-gradient(ellipse at 50% 45%, var(--stage-light) 0%, #c9c9c9 60%, var(--stage-dark) 100%);
    position: relative;
  }
  .card {
    position: absolute;
    width: 374px;
    height: 213px;
    border-radius: 10px;
    overflow: hidden;
  }
  .card--dark { background: var(--ink); color: var(--paper); }
  .card--light { background: var(--paper); color: var(--text-dark); }

  .front-dark { left: 181px; top: 20px; }
  .front-light { left: 595px; top: 20px; }
  .back-list { left: 20px; top: 258px; }
  .back-photo { left: 412px; top: 258px; }
  .back-light { left: 805px; top: 258px; }

  .brand {
    position: absolute;
    display: flex;
    align-items: center;
    gap: 6px;
    font-weight: 800;
    font-size: 16px;
    line-height: 1;
    color: var(--yellow-text);
    white-space: nowrap;
  }
  .brand__dot {
    width: 14px; height: 14px; border-radius: 50%;
    background: var(--yellow);
    flex: none;
  }
  .card--light .brand { color: var(--text-dark); }

  .front .brand { left: 20px; top: 92px; }
  .divider {
    position: absolute; left: 160px; top: 40px;
    width: 1px; height: 118px;
  }
  .card--dark .divider { background: #777; }
  .card--light .divider { background: #bbb; }

  .contact { position: absolute; left: 174px; top: 56px; white-space: nowrap; }
  .contact__name { font-size: 15px; font-weight: 700; line-height: 1.2; }
  .card--dark .contact__name { color: var(--yellow-text); }
  .contact__role { font-size: 11px; line-height: 1.35; margin-top: 1px; }
  .contact__lines { margin-top: 12px; font-size: 10.5px; line-height: 1.5; }
  .contact__line { display: flex; align-items: center; gap: 4px; }
  .contact__line svg { width: 9px; height: 9px; flex: none; }

  .front__bands { position: absolute; left: 0; bottom: 0; width: 374px; height: 36px; }
  .front__web {
    position: absolute; right: 30px; bottom: 5px;
    font-size: 11.5px; line-height: 16px; letter-spacing: 1.6px; color: var(--text-dark);
  }

  .services-title { font-weight: 700; font-size: 15px; }
  .back-list .services-title { position: absolute; top: 50px; width: 100%; text-align: center; color: var(--paper); }
  .grid-list {
    position: absolute; top: 83px; left: 0; width: 100%;
    list-style: none; text-align: center;
    font-size: 12.5px; line-height: 24px; color: var(--yellow-text);
  }
  .grid-list li { display: inline; }
  .grid-list li::before { content: "• "; }
  .grid-list li + li { margin-left: 4px; }
  .tagline {
    position: absolute; bottom: 12px; width: 100%; text-align: center;
    font-weight: 700; font-size: 12.5px; letter-spacing: 0.4px;
  }
  .back-list .tagline { color: var(--paper); }

  .photo-area {
    position: absolute; left: 0; top: 92px; width: 250px; height: 121px;
    background: radial-gradient(ellipse at 40% 55%, #6a6a6a 0%, #2e2e2e 55%, var(--ink) 100%);
  }
  .back-photo .brand { left: 62px; top: 46px; font-size: 13px; }
  .back-photo .services-title { position: absolute; right: 12px; top: 22px; color: var(--paper); }
  .right-list {
    position: absolute; right: 12px; top: 50px; list-style: none; text-align: right;
    font-size: 11.5px; font-weight: 700; line-height: 21px; color: var(--yellow-text);
  }
  .right-list li::before { content: "• "; }

  .back-light .brand { left: 28px; top: 92px; font-size: 17px; }
  .back-light .services-title { position: absolute; left: 190px; top: 20px; color: var(--text-dark); }
  .plain-list {
    position: absolute; left: 190px; top: 48px; list-style: none;
    font-size: 11.5px; line-height: 18px; color: var(--text-muted);
  }
  .plain-list li::before { content: "• "; color: #999; }
  .back-light .tagline { bottom: 10px; left: 0; width: 374px; padding-left: 40px; color: var(--text-dark); letter-spacing: 0.6px; }
</style>
</head>
<body>

<section class="card card--dark front front-dark">
  <div class="brand"><span class="brand__dot"></span>Vigor Ledger</div>
  <div class="divider"></div>
  <div class="contact">
    <p class="contact__name">Marcus Obadiah Lim</p>
    <p class="contact__role">Fitness Coach<br>Corrective Exercise Specialist</p>
    <div class="contact__lines">
      <p class="contact__line"><svg viewBox="0 0 10 10"><rect x="2.5" y="0.5" width="5" height="9" rx="1" fill="#f6d000"/></svg>+65 9437 2065</p>
      <p class="contact__line"><svg viewBox="0 0 10 10"><rect x="0.5" y="2" width="9" height="6" fill="#f6d000"/><path d="M0.5 2 L5 5.5 L9.5 2" stroke="#000" stroke-width="1" fill="none"/></svg>marcus@sgvigorledger-example.com</p>
    </div>
  </div>
  <svg class="front__bands" viewBox="0 0 374 36" aria-hidden="true">
    <polygon points="0,0 176,0 168,8 0,8" fill="#9c9c9c"/>
    <polygon points="188,0 374,0 374,36 0,36 0,13 175,13" fill="#f6d000"/>
  </svg>
  <p class="front__web">www.sgvigor-example.com</p>
</section>

<section class="card card--light front front-light">
  <div class="brand"><span class="brand__dot"></span>Vigor Ledger</div>
  <div class="divider"></div>
  <div class="contact">
    <p class="contact__name">Marcus Obadiah Lim</p>
    <p class="contact__role">Fitness Coach<br>Corrective Exercise Specialist</p>
    <div class="contact__lines">
      <p class="contact__line"><svg viewBox="0 0 10 10"><rect x="2.5" y="0.5" width="5" height="9" rx="1" fill="#333"/></svg>+65 9437 2065</p>
      <p class="contact__line"><svg viewBox="0 0 10 10"><rect x="0.5" y="2" width="9" height="6" fill="#333"/><path d="M0.5 2 L5 5.5 L9.5 2" stroke="#fff" stroke-width="1" fill="none"/></svg>marcus@sgvigorledger-example.com</p>
    </div>
  </div>
  <svg class="front__bands" viewBox="0 0 374 36" aria-hidden="true">
    <polygon points="0,0 176,0 168,8 0,8" fill="#141414"/>
    <polygon points="188,0 374,0 374,36 0,36 0,13 175,13" fill="#f6d000"/>
  </svg>
  <p class="front__web">www.sgvigor-example.com</p>
</section>

<section class="card card--dark back-list">
  <h2 class="services-title">Services</h2>
  <ul class="grid-list">
    <li>Sports Strength &amp; Conditioning</li>
    <li>Sports/Thai Massage</li><br>
    <li>Kettlebell Sport Preparation</li>
    <li>Corrective Exercises</li><br>
    <li>28 days Weight Loss Program</li>
    <li>Calisthenics Training</li><br>
    <li>Myofascial Rehab Therapy</li>
  </ul>
  <p class="tagline">WHAT IS YOUR VIGOR LEDGER?</p>
</section>

<section class="card card--dark back-photo">
  <div class="photo-area" role="img" aria-label="Photo of hex dumbbells on a gym floor"></div>
  <div class="brand"><span class="brand__dot"></span>Vigor Ledger</div>
  <h2 class="services-title">Services</h2>
  <ul class="right-list">
    <li>Sports Strength &amp; Conditioning</li>
    <li>Kettlebell Sport Preparation</li>
    <li>28 days Weight Loss Program</li>
    <li>Myofascial Rehab Therapy</li>
    <li>Calisthenics Training</li>
    <li>Corrective Exercises</li>
    <li>Sports/Thai Massage</li>
  </ul>
</section>

<section class="card card--light back-light">
  <div class="brand"><span class="brand__dot"></span>Vigor Ledger</div>
  <h2 class="services-title">Services</h2>
  <ul class="plain-list">
    <li>Sports Strength &amp; Conditioning</li>
    <li>Kettlebell Sport Preparation</li>
    <li>28 days Weight Loss Program</li>
    <li>Myofascial Rehab Therapy</li>
    <li>Calisthenics Training</li>
    <li>Corrective Exercises</li>
    <li>Sports/Thai Massage</li>
  </ul>
  <p class="tagline">What is your vigor ledger?</p>
</section>

</body>
</html>
```